Exciting & Elegant Stationary Pack

Stationary consists of
1. Letter head / Envelope
2. Business Card
3. Invoice
4. 40x40mm sticker

Attached files;

1. Logo (Other formats available on request)
2. MS word Doc - For information and description of design
3. Website image (This will be our new website so use the colours so everything ties together)
4. Sample of stationary pack we like, but feel free to be creative

Target Market(s)

Home improvement

Industry/Entity Type

Construction

Font styles to use
Other font styles liked:
• Leave up to designer - We like font used on (website attached image)

Requirements
Must have
• Please look at uploaded file of sample website and use colours
Nice to have
• Any type of business card design - eg. metal, die cut, embossed, etc...

```html
<!DOCTYPE html>
<html lang="en">
<head>
<meta charset="utf-8">
<title>Setstone Tiling – Business Card</title>
<link href="https://fonts.googleapis.com/css2?family=Roboto:wght@400;700;900&display=swap" rel="stylesheet">
<style>
  :root{
    --orange:#f0883a;
    --navy:#1d4f7a;
    --navy-deep:#163f63;
    --white:#ffffff;
    --ink:#5a5f66;
    --backdrop:#e7e5e1;
  }
  *{box-sizing:border-box;margin:0;padding:0}
  html,body{width:1200px;height:950px;overflow:hidden;background:var(--backdrop);font-family:"Roboto",Arial,sans-serif}
  .canvas{position:relative;width:1200px;height:950px}
  .card{position:absolute;width:620px;height:354px;overflow:hidden;box-shadow:0 14px 30px rgba(0,0,0,.22)}
  .card--front{left:110px;top:70px;background:var(--orange)}
  .card--back{left:470px;top:520px;background:var(--white)}

  .front__brand{position:absolute;left:0;right:0;top:128px;text-align:center;white-space:nowrap;
    font-weight:900;font-size:44px;color:var(--white);letter-spacing:1px;text-transform:uppercase}
  .front__web{position:absolute;left:0;right:0;bottom:52px;text-align:center;
    font-size:15px;color:var(--white);letter-spacing:5px}

  .back__shapes{position:absolute;inset:0}
  .back__brand{position:absolute;left:392px;top:122px;font-weight:900;font-size:24px;white-space:nowrap;
    color:var(--white);letter-spacing:.5px;text-transform:uppercase}
  .person{position:absolute;left:40px;top:116px}
  .person__name{font-weight:700;font-size:20px;color:var(--navy);text-transform:uppercase;white-space:nowrap}
  .person__role{font-size:14px;color:var(--orange);text-transform:uppercase;margin-top:2px;white-space:nowrap}
  .contact{position:absolute;left:40px;top:192px;font-size:13.5px;color:var(--ink);line-height:23px;white-space:nowrap}
  .contact__row{display:flex;align-items:center;gap:8px}
  .contact__row svg{width:13px;height:13px;flex:none}
  .contact__licence{margin-bottom:8px}
</style>
</head>
<body>
<div class="canvas">

  <section class="card card--front">
    <div class="front__brand">Setstone Tiling</div>
    <div class="front__web">www.setstonetiling.com.au</div>
  </section>

  <section class="card card--back">
    <svg class="back__shapes" viewBox="0 0 620 354" width="620" height="354" aria-hidden="true">
      <polygon points="350,88 545,88 620,128 620,190 380,190" fill="var(--navy)"/>
      <polygon points="0,344 620,250 620,354 0,354" fill="var(--navy-deep)"/>
    </svg>
    <div class="back__brand">Setstone Tiling</div>

    <div class="person">
      <div class="person__name">Linh Tran</div>
      <div class="person__role">Project Manager</div>
    </div>

    <div class="contact">
      <div class="contact__licence">Lic No.,204918c</div>
      <div class="contact__row">
        <svg viewBox="0 0 14 14"><rect x="3.5" y="0.8" width="7" height="12.4" rx="1.3" fill="none" stroke="var(--navy)" stroke-width="1.5"/><circle cx="7" cy="11" r=".9" fill="var(--navy)"/></svg>
        <span>0400 555 019</span>
      </div>
      <div class="contact__row">
        <svg viewBox="0 0 14 14"><rect x="0.8" y="2.5" width="12.4" height="9" fill="var(--navy)"/><polyline points="1,3 7,8 13,3" fill="none" stroke="var(--white)" stroke-width="1.2"/></svg>
        <span>info@setstonetiling.com.au</span>
      </div>
      <div class="contact__row">
        <svg viewBox="0 0 14 14"><circle cx="7" cy="7" r="6.2" fill="var(--navy)"/><ellipse cx="7" cy="7" rx="2.6" ry="6.2" fill="none" stroke="var(--white)" stroke-width="1"/><line x1="1" y1="7" x2="13" y2="7" stroke="var(--white)" stroke-width="1"/></svg>
        <span>www.setstonetiling.com.au</span>
      </div>
    </div>
  </section>

</div>
</body>
</html>
```